Building company buisness cards

We are looking for a sharp modern new look for our business cards.We are a New Zealand based company that specialises in house and land packages.We have attached a photo of the current logo and would like to see if it can be improved somehow if needed.We are open to any colours but we have chosen Black and White at this stage. Feel free to change the font and make the logo smarter looking.Play with the colours and see what looks best.We want a card that looks so good know one will want to throw it away!

Target Market(s)

Building profesonals, home buyers

Industry/Entity Type

Building

Contact Information for Business Card

Garrick Tenwood
0275390628
garrickt@hartvale.co.nz

Font styles to use
Serif
Sans Serif

Colors

Designer to choose colors to be used in the design.

Requirements
Must have
• Just the logo on one side and details on the other
• Clean simple looking card
Nice to have
• Round corners and detail like raised or spot UV
• Something that stands out
Should not have
• To title needed, Director etc

```html
<!DOCTYPE html>
<html lang="en">
<head>
<meta charset="utf-8">
<title>Hartvale Business Card</title>
<link rel="stylesheet" href="https://fonts.googleapis.com/css2?family=Playfair+Display:wght@400;700&family=Raleway:wght@400;500&display=swap">
<style>
  :root {
    --page: #2a2a2a;
    --ink: #141414;
    --card-dark: #1b1b1b;
    --card-light: #ffffff;
    --silver: #cfcfcf;
  }
  * { margin: 0; padding: 0; box-sizing: border-box; }
  html, body {
    width: 1200px; height: 895px; overflow: hidden;
    background: var(--page);
  }
  .canvas {
    position: relative; width: 1200px; height: 895px;
    display: flex; flex-direction: column; align-items: center; justify-content: center; gap: 40px;
  }
  .card {
    position: relative; width: 680px; height: 389px;
    border-radius: 14px; overflow: hidden;
    box-shadow: 0 12px 30px rgba(0,0,0,.45);
  }
  .brand-name {
    font-family: "Playfair Display", serif; font-weight: 700;
    line-height: 1; letter-spacing: -1px;
  }

  /* Front */
  .card--front {
    background: var(--card-dark);
    display: flex; align-items: center; justify-content: center;
  }
  .card--front .brand-name { font-size: 84px; color: var(--silver); }

  /* Back */
  .card--back { background: var(--card-light); }
  .back-brand {
    position: absolute; top: 48px; left: 0; right: 0;
    display: flex; justify-content: center;
  }
  .back-brand .brand-name { font-size: 56px; color: var(--ink); }
  .name-band {
    position: absolute; top: 178px; left: 30px; right: 0; height: 46px;
    background: var(--ink);
    display: flex; align-items: center; padding-left: 200px;
  }
  .name-band__text {
    font-family: "Playfair Display", serif; font-size: 28px; line-height: 1;
    color: var(--card-light); letter-spacing: .5px; white-space: nowrap;
  }
  .contacts {
    position: absolute; left: 40px; right: 40px; bottom: 52px;
    display: flex; justify-content: space-between; align-items: center;
  }
  .contact { display: flex; align-items: center; gap: 12px; }
  .contact__icon { width: 32px; height: 32px; flex: none; }
  .contact__text {
    font-size: 22px; line-height: 1; color: var(--ink); white-space: nowrap;
  }
  .contact__text--phone { font-family: "Raleway", sans-serif; }
  .contact__text--email { font-family: "Playfair Display", serif; }
</style>
</head>
<body>
<main class="canvas">
  <section class="card card--front">
    <span class="brand-name">Hartvale</span>
  </section>

  <section class="card card--back">
    <div class="back-brand">
      <span class="brand-name">Hartvale</span>
    </div>
    <div class="name-band"><span class="name-band__text">Garrick Tenwood</span></div>
    <div class="contacts">
      <div class="contact">
        <svg class="contact__icon" viewBox="0 0 32 32" aria-hidden="true">
          <circle cx="16" cy="16" r="14.5" fill="none" stroke="#141414" stroke-width="2.5"/>
          <path d="M11 9.5c.8-.6 1.8-.4 2.3.4l1.4 2.3c.4.7.2 1.5-.4 2l-1 .8c.8 1.8 2 3 3.8 3.8l.8-1c.5-.6 1.3-.8 2-.4l2.3 1.4c.8.5 1 1.5.4 2.3l-.8 1c-.8.9-2 1.2-3.2.8-4.1-1.4-7.2-4.5-8.6-8.6-.4-1.2 0-2.4.8-3.2z" fill="#141414"/>
        </svg>
        <span class="contact__text contact__text--phone">0275390628</span>
      </div>
      <div class="contact">
        <svg class="contact__icon" viewBox="0 0 32 32" aria-hidden="true">
          <circle cx="16" cy="16" r="14.5" fill="#141414"/>
          <rect x="8.5" y="10.5" width="15" height="11" rx="1" fill="none" stroke="#fff" stroke-width="1.8"/>
          <path d="M8.5 11l7.5 6 7.5-6" fill="none" stroke="#fff" stroke-width="1.8"/>
        </svg>
        <span class="contact__text contact__text--email">garrickt@hartvale.co.nz</span>
      </div>
    </div>
  </section>
</main>
</body>
</html>
```